Business Card Design - Amberfield Court

We are looking at a new design for our business cards that has a modern and professional look. We run a residential aged care facility focussing on the care of residents. The cards will be used for potential clients, consultants and business opportunities in this sector. Blue and white is our main colours and would to see these colours incorporated in the design.
Industry/Entity Type
Business
Contact Information for Business Card
Amberfield Court, Darren Walsh, dwalsh@amberfieldcourt.com.au, Finance Manager, 0472 639 208, BCom, 37 Marrabel Crescent, Brindle Vale, Qld 4093.
Look and feel
Each slider illustrates characteristics of the customer's brand and the style your logo design should communicate.

```html
<!DOCTYPE html>
<html lang="en">
<head>
<meta charset="utf-8">
<title>Amberfield Court – Business Card</title>
<link rel="stylesheet" href="https://fonts.googleapis.com/css2?family=Open+Sans:wght@400;600;700&display=swap">
<style>
  :root {
    --navy: #1f3c4c;
    --steel: #4a7d9c;
    --white: #ffffff;
    --ghost: #e6e8ea;
    --ink: #2a3a44;
    --stage: #e9ecef;
    --marker: #b9a99a;
  }
  * { box-sizing: border-box; margin: 0; padding: 0; }
  html, body { width: 1200px; height: 900px; overflow: hidden; }
  body {
    background: var(--stage);
    font-family: "Open Sans", Arial, sans-serif;
    position: relative;
  }
  .card {
    position: absolute;
    width: 540px;
    height: 310px;
    border-radius: 18px;
    overflow: hidden;
    box-shadow: 0 10px 28px rgba(0,0,0,.18);
  }
  /* front */
  .card-front { left: 90px; top: 110px; background: var(--navy); }
  .front-lockup {
    position: absolute; left: 0; right: 0; top: 50%;
    transform: translateY(-50%);
    display: flex; flex-direction: column; align-items: center;
  }
  .brand-row { display: flex; align-items: center; gap: 14px; }
  .brand-dot { width: 34px; height: 34px; border-radius: 50%; background: var(--white); flex: none; }
  .brand-name {
    color: var(--white); font-weight: 600; font-size: 30px;
    letter-spacing: 3px; text-transform: uppercase; white-space: nowrap;
  }
  .tagline-bar {
    margin-top: 12px; background: var(--steel); color: var(--white);
    font-size: 17px; padding: 3px 18px; letter-spacing: .3px; white-space: nowrap;
  }
  /* back */
  .card-back { left: 570px; top: 480px; background: var(--white); }
  .ghost-name {
    position: absolute; left: 26px; top: 54px;
    color: var(--ghost); font-weight: 600; font-size: 26px;
    letter-spacing: 3px; text-transform: uppercase; white-space: nowrap;
  }
  .band {
    position: absolute; left: 0; right: 0; top: 118px; height: 84px;
    background: var(--steel);
  }
  .band-notch {
    position: absolute; left: 0; top: 156px; width: 34px; height: 46px;
    background: var(--white);
  }
  .band-marker {
    position: absolute; left: 22px; top: 163px; width: 7px; height: 18px;
    background: var(--marker);
  }
  .holder { position: absolute; left: 50px; top: 150px; color: var(--white); }
  .holder-name { font-weight: 700; font-size: 25px; letter-spacing: .5px; line-height: 1; white-space: nowrap; }
  .holder-role { font-size: 12.5px; margin-top: 4px; letter-spacing: .4px; white-space: nowrap; }
  .back-lockup {
    position: absolute; right: 22px; top: 128px;
    display: flex; flex-direction: column; align-items: center;
  }
  .back-lockup .brand-row { gap: 7px; }
  .back-lockup .brand-dot { width: 14px; height: 14px; }
  .back-lockup .brand-name { font-size: 13px; letter-spacing: 1.5px; }
  .back-lockup .tagline { color: var(--white); font-size: 9px; margin-top: 4px; white-space: nowrap; }
  .address {
    position: absolute; right: 26px; top: 214px; text-align: right;
    color: var(--ink); font-size: 13.5px; line-height: 1.45;
  }
  .contacts {
    position: absolute; left: 50px; bottom: 30px;
    color: var(--ink); font-size: 13.5px; line-height: 1.6;
  }
  .contact-line { display: flex; align-items: center; gap: 8px; }
  .contact-line svg { width: 12px; height: 12px; fill: var(--ink); }
</style>
</head>
<body>
  <section class="card card-front">
    <div class="front-lockup">
      <div class="brand-row">
        <span class="brand-dot"></span>
        <span class="brand-name">Amberfield Court</span>
      </div>
      <div class="tagline-bar">Comfort, Respect, Belonging</div>
    </div>
  </section>

  <section class="card card-back">
    <div class="ghost-name" aria-hidden="true">Amberfield Court</div>
    <div class="band"></div>
    <div class="band-notch"></div>
    <div class="band-marker"></div>

    <div class="holder">
      <div class="holder-name">DARREN WALSH</div>
      <div class="holder-role">FINANCE MANAGER (BCOM)</div>
    </div>

    <div class="back-lockup">
      <div class="brand-row">
        <span class="brand-dot"></span>
        <span class="brand-name">Amberfield Court</span>
      </div>
      <div class="tagline">Comfort, Respect, Belonging</div>
    </div>

    <div class="address">
      37 Marrabel Crescent<br>Brindle Vale, Qld 4093
    </div>

    <div class="contacts">
      <div class="contact-line">
        <svg viewBox="0 0 24 24" aria-hidden="true"><path d="M6.6 10.8a15.1 15.1 0 0 0 6.6 6.6l2.2-2.2a1 1 0 0 1 1-.25 11.4 11.4 0 0 0 3.6.57 1 1 0 0 1 1 1V20a1 1 0 0 1-1 1A17 17 0 0 1 3 4a1 1 0 0 1 1-1h3.5a1 1 0 0 1 1 1c0 1.25.2 2.45.57 3.57a1 1 0 0 1-.25 1z"/></svg>
        <span>0472 639 208</span>
      </div>
      <div class="contact-line">
        <svg viewBox="0 0 24 24" aria-hidden="true"><path d="M2 5h20v14H2zm2 2v.5l8 5 8-5V7zm0 2.8V17h16V9.8l-8 5z"/></svg>
        <span>dwalsh@amberfieldcourt.com.au</span>
      </div>
    </div>
  </section>
</body>
</html>
```